Small corporate website template design

I need a couple templates designed for a small corporate website. The corporate site reflects the existence of the parent company which will own various brands/services that have their own websites, so it will mainly be used to present who we are, what we do, what is happening (news/events), how to contact us, link off to our other brand/service sites, as well as post information for public relations, investors, and job opportunities.

The company name is Brelvanto LLC (www.brelvanto-example.com), and the name is representative of stratified layers of interconnected digital services. The corporate site is not expected to generate a bunch of fanfare - that honor will be reserved for the externally linked brand/service sites.

The provided logo may be manipulated in color, size, shape, positioning, etc. to get it to fit with the design, but should be integrated in some way.

What we are looking for is a home page layout as well as a template for an inner page whereby the navigation/logo, etc may be diminished to some extent for the inner pages. We are also interested in reusable elements such as dividers, content containers, etc. in order to represent the types of information described above that we would like to present as described above.

We are particularly interested in consistency of design elements, conservative use of color (including consideration of accessibility concerns), judicious use of whitespace in favor of simplified messaging, and something lending itself well to internationalization/translation.

Target Market(s)

Small business owners, entrepreneurs (B2B)

Number of Pages Required

2 page

Font styles to use
Sans Serif

Requirements
Must have
• See the attached PDF with the logo concept, color swatches, and comparative sites.

```html
<!DOCTYPE html>
<html lang="en">
<head>
<meta charset="utf-8">
<title>Brelvanto LLC</title>
<link href="https://fonts.googleapis.com/css2?family=Montserrat:wght@500;600;700&family=Open+Sans:wght@400;600;700&display=swap" rel="stylesheet">
<style>
:root{
  --orange:#ff9900;
  --white:#ffffff;
  --ink:#333333;
  --body:#555555;
  --grey-band:#ededed;
  --footer:#333333;
  --footer-base:#242424;
  --footer-text:#e6e6e6;
}
*{margin:0;padding:0;box-sizing:border-box}
html,body{width:1200px;height:2719px;overflow:hidden;background:var(--white)}
body{position:relative;font-family:"Open Sans",Arial,sans-serif;color:var(--body)}
.abs{position:absolute}
.hero{left:0;top:0;width:1200px;height:780px;background:linear-gradient(180deg,var(--orange) 0%,var(--orange) 52%,#ffd9a0 75%,var(--white) 100%)}
.brand{font-family:"Open Sans",Arial,sans-serif;font-weight:700;font-size:28px;color:var(--white);display:flex;align-items:center;gap:12px}
.brand .mark{width:22px;height:22px;background:var(--white)}
.nav{left:384px;top:40px;display:flex;gap:32px;font-family:"Montserrat",Arial,sans-serif;font-size:16px;color:var(--white);letter-spacing:.3px}
.btn{display:flex;align-items:center;justify-content:center;font-family:"Montserrat",Arial,sans-serif;font-weight:700;font-size:19px;letter-spacing:.4px}
.btn-light{background:var(--white);color:var(--orange)}
.btn-orange{background:var(--orange);color:var(--white)}
.hero-title{left:78px;top:275px;font-family:"Montserrat",Arial,sans-serif;font-weight:600;font-size:46px;color:var(--white)}
.hero-sub{left:80px;top:348px;font-family:"Open Sans",Arial,sans-serif;font-weight:700;font-size:23px;line-height:36px;color:var(--white)}
.art{border-radius:6px}
.card{background:var(--white);box-shadow:0 3px 14px rgba(0,0,0,.12);text-align:center}
.card .icon{margin:50px auto 0;width:90px;height:90px;border-radius:50%}
.card h3{margin-top:46px;font-family:"Open Sans",Arial,sans-serif;font-weight:600;font-size:19.5px;color:var(--ink)}
.card p{margin:10px auto 0;width:290px;font-size:14.5px;line-height:25px;color:var(--body)}
.sec-title{font-family:"Montserrat",Arial,sans-serif;font-weight:700;font-size:40px;color:var(--orange)}
.copy p{font-size:14px;line-height:25px;color:var(--body);margin-bottom:13px}
.band{left:0;top:1438px;width:1200px;height:459px;background:var(--grey-band)}
.testimonial{left:607px;top:1568px;width:520px}
.quote{font-weight:700;font-size:18.5px;line-height:31px;color:#4a4a4a}
.client{margin-top:18px;font-size:14.5px;color:var(--body)}
.avatars{display:flex;align-items:center;gap:6px;margin-top:22px}
.avatar{border-radius:50%;background:linear-gradient(135deg,#c9a27f,#7a5a44)}
.news{background:var(--white);box-shadow:0 3px 14px rgba(0,0,0,.12);padding:24px 14px 22px 14px}
.news .date{display:flex;align-items:center;gap:14px;font-size:16px;color:var(--body)}
.news h4{margin-top:20px;font-weight:700;font-size:18px;color:var(--ink);white-space:nowrap}
.news p{margin-top:10px;font-size:14px;line-height:25px;color:var(--body)}
.footer{left:0;top:2375px;width:1200px;height:290px;background:var(--footer)}
.footer-base{left:0;top:2665px;width:1200px;height:54px;background:var(--footer-base);color:var(--footer-text);font-size:14.5px;display:flex;align-items:center;justify-content:center}
.f-head{font-family:"Montserrat",Arial,sans-serif;font-weight:600;font-size:24px;color:var(--white)}
.f-text{font-size:14.5px;line-height:25px;color:var(--footer-text)}
.f-links{list-style:none}
.f-links li{font-size:14.5px;line-height:32.5px;color:var(--footer-text)}
.contact-row{display:flex;gap:18px;align-items:flex-start}
</style>
</head>
<body>

<div class="abs hero"></div>

<header>
  <div class="abs brand" style="left:78px;top:36px"><span class="mark"></span>Brelvanto LLC</div>
  <nav class="abs nav"><span>HOME</span><span>ABOUT</span><span>SERVICES</span><span>NEWS</span><span>CONTACT</span></nav>
  <div class="abs btn btn-light" style="left:955px;top:29px;width:167px;height:47px">GET STARTED</div>
</header>

<section>
  <h1 class="abs hero-title">Brelvanto LLC</h1>
  <p class="abs hero-sub">Adaptive Software Technology for<br>the Digital Revolution</p>
  <div class="abs art" role="img" aria-label="Illustration of a developer working at a desk with monitors, lamp and plants" style="left:598px;top:145px;width:526px;height:372px;background:linear-gradient(160deg,#ffb84d,#e88400)"></div>
</section>

<section>
  <div class="abs card" style="left:78px;top:629px;width:323px;height:312px">
    <div class="icon" role="img" aria-label="Target with arrow icon" style="background:#e04848"></div>
    <h3>Marketing Strategy</h3>
    <p>Lorem Ipsum is simply dummy text of the printing and typesetting industry. Lorem Ipsum has been the industry.</p>
  </div>
  <div class="abs card" style="left:439px;top:629px;width:323px;height:312px">
    <div class="icon" role="img" aria-label="Presentation board with chart icon" style="background:#5a8fb8"></div>
    <h3>Digital Analytics</h3>
    <p>Lorem Ipsum is simply dummy text of the printing and typesetting industry. Lorem Ipsum has been the industry.</p>
  </div>
  <div class="abs card" style="left:800px;top:629px;width:323px;height:312px">
    <div class="icon" role="img" aria-label="Browser window with gear icon" style="background:#3f8fd8"></div>
    <h3>Management and Optimization</h3>
    <p>Lorem Ipsum is simply dummy text of the printing and typesetting industry. Lorem Ipsum has been the industry.</p>
  </div>
</section>

<section>
  <h2 class="abs sec-title" style="left:78px;top:1042px">Welcome to Brelvanto LLC</h2>
  <div class="abs copy" style="left:78px;top:1102px;width:570px">
    <p>Lorem Ipsum is simply dummy text of the printing and typesetting industry. Lorem Ipsum has been the industry's standard dummy text ever since the 1500s, when an unknown printer took a galley of type and scrambled it to make a type specimen book.</p>
    <p>It has survived not only five centuries, but also the leap into electronic typesetting, remaining essentially unchanged. It was popularised in the 1960s with the release of Letraset sheets containing Lorem Ipsum passages, and more recently.</p>
  </div>
  <div class="abs btn btn-orange" style="left:78px;top:1309px;width:167px;height:45px">KNOW MORE</div>
  <div class="abs art" role="img" aria-label="Isometric illustration of a tablet with business charts, figures and a briefcase" style="left:707px;top:1024px;width:417px;height:335px;background:linear-gradient(150deg,#6ab0e8,#2f4d7a)"></div>
</section>

<section>
  <div class="abs band"></div>
  <div class="abs" role="img" aria-label="Photo of a businesswoman working on a laptop in an office" style="left:0;top:1438px;width:598px;height:459px;background:linear-gradient(90deg,#c9c9c9,#ededed)"></div>
  <h2 class="abs sec-title" style="left:607px;top:1510px">Testimonials</h2>
  <div class="abs testimonial">
    <p class="quote">Lorem Ipsum is simply dummy text of the printing and typesetting industry. Lorem Ipsum has been the industry's standard dummy text ever since the 1500s.</p>
    <p class="client">Client Name / Info</p>
    <div class="avatars">
      <div class="avatar" role="img" aria-label="Client portrait" style="width:73px;height:73px;border:3px solid var(--orange)"></div>
      <div class="avatar" role="img" aria-label="Client portrait" style="width:63px;height:63px"></div>
      <div class="avatar" role="img" aria-label="Client portrait" style="width:63px;height:63px"></div>
    </div>
  </div>
</section>

<section>
  <h2 class="abs sec-title" style="left:0;top:1944px;width:1200px;text-align:center">Latest News</h2>
  <article class="abs news" style="left:78px;top:2008px;width:499px">
    <div class="date"><svg width="20" height="20" viewBox="0 0 20 20"><rect x="1" y="3" width="18" height="16" fill="none" stroke="#ff9900" stroke-width="2"/><rect x="1" y="3" width="18" height="5" fill="#ff9900"/><rect x="5" y="0" width="2" height="5" fill="#ff9900"/><rect x="13" y="0" width="2" height="5" fill="#ff9900"/></svg>25 FEB 2018</div>
    <h4>Lorem Ipsum is simply dummy text of the printing</h4>
    <p>Lorem Ipsum is simply dummy text of the printing and typesetting industry. Lorem Ipsum has been the industry's standard dummy text ever since the 1500s, when an unknown printer took a galley.</p>
  </article>
  <article class="abs news" style="left:624px;top:2008px;width:500px">
    <div class="date"><svg width="20" height="20" viewBox="0 0 20 20"><rect x="1" y="3" width="18" height="16" fill="none" stroke="#ff9900" stroke-width="2"/><rect x="1" y="3" width="18" height="5" fill="#ff9900"/><rect x="5" y="0" width="2" height="5" fill="#ff9900"/><rect x="13" y="0" width="2" height="5" fill="#ff9900"/></svg>25 FEB 2018</div>
    <h4>Lorem Ipsum is simply dummy text of the printing</h4>
    <p>Lorem Ipsum is simply dummy text of the printing and typesetting industry. Lorem Ipsum has been the industry's standard dummy text ever since the 1500s, when an unknown printer took a galley.</p>
  </article>
  <div class="abs btn btn-orange" style="left:502px;top:2253px;width:196px;height:44px">EXPLORE MORE</div>
</section>

<footer>
  <div class="abs footer"></div>
  <div class="abs brand" style="left:78px;top:2440px;color:var(--orange)"><span class="mark" style="background:var(--orange)"></span>Brelvanto LLC</div>
  <p class="abs f-text" style="left:78px;top:2522px;width:300px">Lorem Ipsum is simply dummy text of the printing and typesetting industry. Lorem Ipsum has been the industry's standard.</p>

  <h5 class="abs f-head" style="left:441px;top:2424px">Site Map</h5>
  <ul class="abs f-links" style="left:441px;top:2460px">
    <li>Home</li><li>About</li><li>Services</li><li>News</li><li>Contact</li>
  </ul>

  <h5 class="abs f-head" style="left:803px;top:2424px">Contact Info</h5>
  <div class="abs contact-row" style="left:800px;top:2464px">
    <svg width="20" height="26" viewBox="0 0 20 26"><path d="M10 0C4.5 0 0 4.4 0 9.8 0 17 10 26 10 26s10-9 10-16.2C20 4.4 15.5 0 10 0z" fill="#ff9900"/><circle cx="10" cy="10" r="4" fill="#333"/></svg>
    <p class="f-text" style="width:230px">Lorem Ipsum is simply dummy text of the printing.</p>
  </div>
  <div class="abs contact-row" style="left:800px;top:2529px">
    <svg width="20" height="20" viewBox="0 0 24 24"><path d="M6.6 10.8a15.1 15.1 0 0 0 6.6 6.6l2.2-2.2c.3-.3.7-.4 1-.2 1.1.4 2.3.6 3.6.6.6 0 1 .4 1 1V20c0 .6-.4 1-1 1A17 17 0 0 1 3 4c0-.6.4-1 1-1h3.5c.6 0 1 .4 1 1 0 1.3.2 2.5.6 3.6.1.3 0 .7-.2 1z" fill="#ff9900"/></svg>
    <p class="f-text">123 456 7890</p>
  </div>
  <div class="abs contact-row" style="left:800px;top:2570px">
    <svg width="20" height="16" viewBox="0 0 20 16" style="margin-top:5px"><rect width="20" height="16" fill="#ff9900"/><path d="M0 0l10 8 10-8" fill="none" stroke="#333" stroke-width="1.6"/></svg>
    <p class="f-text">info@brelvanto-example.com</p>
  </div>

  <div class="abs footer-base">©Brelvanto LLC, 2018. All Rights Reserved.</div>
</footer>

</body>
</html>
```